Business Card for Lantern Reach

Please design a Modern Business card for a Online Marketing Company

Website: http://www.lanternreach-example.com.au

Please do NOT include physical address in design.

```html
<!DOCTYPE html>
<html lang="en">
<head>
<meta charset="utf-8">
<title>Lantern Reach – Business Card</title>
<link href="https://fonts.googleapis.com/css2?family=Open+Sans:wght@400;600&display=swap" rel="stylesheet">
<style>
  :root {
    --canvas-bg: #ecebe8;
    --card-bg: #ffffff;
    --ink-dark: #1f1f1f;
    --ink-mid: #3a3a3a;
    --ink-soft: #666666;
    --divider: #cfd3d6;
  }
  * { margin: 0; padding: 0; box-sizing: border-box; }
  html, body { width: 1200px; height: 466px; overflow: hidden; }
  body {
    background: var(--canvas-bg);
    font-family: "Open Sans", Arial, sans-serif;
    display: flex;
    align-items: center;
    justify-content: center;
    gap: 60px;
  }
  .card {
    width: 520px;
    height: 300px;
    background: var(--card-bg);
    border-radius: 30px;
    box-shadow: 0 6px 18px rgba(0,0,0,0.12);
    position: relative;
  }

  /* Front: name block + contact */
  .card--front { display: flex; align-items: center; }
  .brand-block {
    width: 230px;
    padding-left: 40px;
    padding-top: 70px;
  }
  .brand-name {
    display: flex;
    align-items: center;
    gap: 8px;
    font-weight: 600;
    color: var(--ink-dark);
    font-size: 20px;
    white-space: nowrap;
  }
  .brand-square {
    width: 12px; height: 12px;
    background: var(--ink-dark);
    flex: none;
  }
  .brand-tagline {
    font-weight: 400;
    color: var(--ink-soft);
    font-size: 11px;
    margin-top: 3px;
    padding-left: 20px;
    white-space: nowrap;
  }
  .divider {
    width: 1px;
    height: 140px;
    background: var(--divider);
    margin-left: 14px;
  }
  .contact-block { padding-left: 26px; padding-top: 8px; }
  .person-name { font-weight: 600; font-size: 18px; color: var(--ink-dark); }
  .person-title { font-size: 13px; color: var(--ink-soft); margin-bottom: 38px; }
  .contact-list { list-style: none; }
  .contact-item {
    display: flex;
    align-items: center;
    gap: 8px;
    font-size: 12.5px;
    color: var(--ink-mid);
    line-height: 20px;
    white-space: nowrap;
  }
  .contact-icon { width: 11px; height: 11px; flex: none; fill: var(--ink-mid); }

  /* Back: centred name */
  .card--back {
    display: flex;
    flex-direction: column;
    align-items: center;
    justify-content: flex-end;
    padding-bottom: 48px;
  }
  .card--back .brand-name { font-size: 34px; gap: 12px; }
  .card--back .brand-square { width: 20px; height: 20px; }
  .card--back .brand-tagline { font-size: 15px; padding-left: 32px; margin-top: 2px; }
  .back-website {
    margin-top: 30px;
    font-size: 18px;
    letter-spacing: 0.6px;
    color: var(--ink-mid);
  }
</style>
</head>
<body>
  <section class="card card--front">
    <div class="brand-block">
      <div class="brand-name"><span class="brand-square"></span>Lantern Reach</div>
      <div class="brand-tagline">Clear plans for digital growth</div>
    </div>
    <div class="divider"></div>
    <div class="contact-block">
      <div class="person-name">Your Name</div>
      <div class="person-title">Title</div>
      <ul class="contact-list">
        <li class="contact-item">
          <svg class="contact-icon" viewBox="0 0 24 24"><path d="M6.6 10.8a15.1 15.1 0 0 0 6.6 6.6l2.2-2.2c.3-.3.7-.4 1-.2 1.1.4 2.3.6 3.6.6.6 0 1 .4 1 1V20c0 .6-.4 1-1 1A17 17 0 0 1 3 4c0-.6.4-1 1-1h3.5c.6 0 1 .4 1 1 0 1.3.2 2.5.6 3.6.1.3 0 .7-.2 1z"/></svg>
          0491 570 156
        </li>
        <li class="contact-item">
          <svg class="contact-icon" viewBox="0 0 24 24"><path d="M2 5h20v14H2z M4 7v.4l8 5 8-5V7z" fill-rule="evenodd"/></svg>
          hello@lanternreach-example.com.au
        </li>
        <li class="contact-item">
          <svg class="contact-icon" viewBox="0 0 24 24"><path d="M12 2a10 10 0 1 0 0 20 10 10 0 0 0 0-20zm6.9 6h-2.9a15 15 0 0 0-1.4-3.6A8 8 0 0 1 18.9 8zM12 4c.8 1.2 1.5 2.5 1.9 4h-3.8c.4-1.5 1.1-2.8 1.9-4zM4.3 14a8 8 0 0 1 0-4h3.4a16 16 0 0 0 0 4zm.8 2h2.9c.3 1.3.8 2.5 1.4 3.6A8 8 0 0 1 5.1 16zM8 8H5.1a8 8 0 0 1 4.3-3.6C8.8 5.5 8.3 6.7 8 8zm4 12c-.8-1.2-1.5-2.5-1.9-4h3.8c-.4 1.5-1.1 2.8-1.9 4zm2.3-6H9.7a14 14 0 0 1 0-4h4.6a14 14 0 0 1 0 4zm.3 5.6c.6-1.1 1.1-2.3 1.4-3.6h2.9a8 8 0 0 1-4.3 3.6zm1.7-5.6a16 16 0 0 0 0-4h3.4a8 8 0 0 1 0 4z"/></svg>
          www.lanternreach-example.com.au
        </li>
      </ul>
    </div>
  </section>

  <section class="card card--back">
    <div class="brand-name"><span class="brand-square"></span>Lantern Reach</div>
    <div class="brand-tagline">Clear plans for digital growth</div>
    <div class="back-website">www.lanternreach-example.com.au</div>
  </section>
</body>
</html>
```